Website Design Request - Management Consulting Firm

We need a Website designed for an IT Management Staffing and Recruiting firm called TRAVENOK based in San Francisco.

The firm is an high-end technology staffing agency. Our focus is on quality and high-caliber candidates rather than quantity.

The website will have two main home pages. One for the recruiter and another on for the candidates.

The website needs to optimize for mobile devices as well.

I have attached few mock-ups that I have done just to show what I am thinking. The UI needs to be very clean, fluid, and it needs to have a modern, rustic, professional feel to it.

Target Market(s)

Technology Manager, Director, VP, CIO of Companies that have $4b-10b dollar revenue. Such as larkspurdwellings.example , https://www.velmorian.example/, quillnet.example, zib.example

Industry/Entity Type

Management Consulting

Number of Pages Required

5+ page

Font styles to use
Sans Serif

Colors
f37122
ffffff

Requirements
Must have
• Please review mock-ups for suggestions
Nice to have
Should not have

```html
<!DOCTYPE html>
<html lang="en">
<head>
<meta charset="utf-8">
<title>TRAVENOK — IT Project Management Jobs</title>
<link rel="stylesheet" href="https://fonts.googleapis.com/css2?family=Mulish:wght@400;600;700&family=Open+Sans:wght@400;600&display=swap">
<style>
:root{
  --orange:#f37122;
  --white:#ffffff;
  --ink:#3d3d3d;
  --muted:#777777;
  --dark-tab:#515151;
  --footer-bg:#f2f2f2;
  --line:#d8d8d8;
}
*{box-sizing:border-box;margin:0;padding:0}
html,body{width:744px;height:1200px;overflow:hidden;background:var(--white)}
body{position:relative;font-family:"Open Sans",sans-serif;color:var(--ink)}
.abs{position:absolute}
.brand{font-family:"Mulish",sans-serif;font-weight:700;color:var(--orange);letter-spacing:1px}
.site-header .brand{left:70px;top:21px;font-size:24px}
.main-nav{left:344px;top:25px;display:flex;align-items:center;font-size:7.5px;text-transform:uppercase;color:#444}
.main-nav a{color:inherit;text-decoration:none;margin-right:35px}
.main-nav a.active{color:var(--orange);border:1px solid var(--orange);border-radius:2px;padding:8px 14px;margin-right:21px}
.main-nav a:last-child{margin-right:0}
.hero{left:0;top:74px;width:744px;height:326px}
.hero-photo{position:absolute;inset:0;background:linear-gradient(90deg,#eef0f3 0%,#e2e6ec 45%,#c9ced6 70%,#a9a6a3 85%,#d6d8dc 100%)}
.hero h1{position:absolute;top:105px;left:0;width:744px;text-align:center;font-family:"Mulish",sans-serif;font-weight:600;font-size:21px;color:#333}
.hero .lead{position:absolute;top:147px;width:744px;text-align:center;font-size:10px;color:#666}
.signup-field{position:absolute;left:187px;top:183px;width:236px;height:37px;background:#f3f4f6;border:1px solid #cfd2d6;border-radius:2px;font-size:7.5px;color:#777;padding:13px 16px}
.signup-btn{position:absolute;left:439px;top:183px;width:118px;height:37px;background:var(--orange);color:var(--white);font-size:8px;font-weight:600;text-align:center;line-height:37px;border-radius:2px}
.employer-note{position:absolute;top:237px;width:744px;text-align:center;font-size:7.5px;color:#555}
.employer-note span{text-decoration:underline;color:#333;margin-left:4px}
.slider-dots{position:absolute;top:302px;left:357px;display:flex;gap:7px}
.slider-dots i{width:5px;height:5px;border-radius:50%;background:#999}
.slider-dots i.on{background:#555}
.tabs{left:69px;top:432px;width:605px;height:43px;display:flex;font-family:"Mulish",sans-serif;font-weight:600;font-size:12px;color:var(--white)}
.tab{flex:1;display:flex;align-items:center;justify-content:center;position:relative}
.tab-dark{background:var(--dark-tab)}
.tab-active{background:var(--orange)}
.tab-active::after{content:"";position:absolute;bottom:-8px;left:50%;margin-left:-6px;border:6px solid transparent;border-top:8px solid var(--orange);border-bottom:0}
.section-title{top:515px;width:744px;text-align:center;font-family:"Mulish",sans-serif;font-weight:600;font-size:12px;color:#444}
.feature{width:300px;text-align:center}
.feature .icon{display:block;margin:0 auto;width:38px;height:38px}
.feature h3{font-family:"Mulish",sans-serif;font-weight:600;font-size:10px;color:#333;margin-top:14px}
.feature p{font-size:7.2px;line-height:16px;color:var(--muted);margin-top:10px}
.resume-btn{left:298px;top:874px;width:148px;height:38px;border:1px solid var(--orange);border-radius:2px;color:var(--orange);font-family:"Mulish",sans-serif;font-weight:600;font-size:10px;text-align:center;line-height:36px}
.site-footer{left:0;top:959px;width:744px;height:190px;background:var(--footer-bg)}
.site-footer h4{font-family:"Mulish",sans-serif;font-weight:600;font-size:12px;color:#333}
.footer-about{left:69px;top:26px;width:215px}
.footer-about .brand{font-size:29px;margin-top:8px;line-height:1.1}
.tagline{font-size:7.5px;letter-spacing:.5px;color:#333;margin-top:1px}
.footer-about p{font-size:6.5px;line-height:14px;color:var(--muted);margin-top:14px}
.quick-links{left:359px;top:26px}
.quick-links ul{list-style:none;margin-top:7px}
.quick-links li{font-size:6.5px;color:var(--muted);line-height:16px}
.footer-contact{left:520px;top:26px;width:155px}
.footer-contact p{font-size:6.5px;line-height:13px;color:var(--muted);margin-top:7px}
.contact-line{display:flex;align-items:center;gap:7px;font-size:6.5px;color:#333;margin-top:13px}
.contact-line + .contact-line{margin-top:10px}
.bottom-bar{left:0;top:1149px;width:744px;height:51px}
.copyright{position:absolute;left:69px;top:22px;font-size:6.5px;color:var(--muted)}
.social{position:absolute;left:601px;top:20px;display:flex;gap:11px}
.social i{width:11px;height:11px;border-radius:50%;background:#777}
</style>
</head>
<body>

<header class="site-header">
  <div class="brand abs">TRAVENOK</div>
  <nav class="main-nav abs">
    <a class="active">Home</a><a>Professionals</a><a>Employers</a><a>Sign In</a><a>Sign Up</a>
  </nav>
</header>

<section class="hero abs">
  <div class="hero-photo" role="img" aria-label="Photo of a woman on a phone call working at a laptop by a bright window, with a coffee cup"></div>
  <h1>Looking for IT Project Management Jobs?</h1>
  <p class="lead">Upload your resume, accept interview requests, get offers</p>
  <div class="signup-field">Email Address</div>
  <div class="signup-btn">GET OFFERS NOW</div>
  <p class="employer-note">Looking for talents? <span>See how it works for Employers</span></p>
  <div class="slider-dots"><i></i><i class="on"></i><i></i></div>
</section>

<div class="tabs abs">
  <div class="tab tab-dark">How it works?</div>
  <div class="tab tab-active">Why Us?</div>
</div>

<h2 class="section-title abs">Why Professionals Love us</h2>

<div class="feature abs" style="left:66px;top:562px">
  <svg class="icon" viewBox="0 0 38 38" role="img" aria-label="Pay card icon"><rect x="4" y="12" width="30" height="20" rx="2" fill="#3a8fc7"/><rect x="4" y="16" width="30" height="4" fill="#1f5f8b"/><path d="M10 12l10-8 8 8z" fill="#8cc63f"/></svg>
  <h3>Get Paid More</h3>
  <p>On average, TRAVENOK candidates get upto 20% more for their skills. Our talent engines makes you discoverable for your niche project experiences.</p>
</div>

<div class="feature abs" style="left:376px;top:562px">
  <svg class="icon" viewBox="0 0 38 38" role="img" aria-label="Phone icon"><path d="M9 4l6 0 3 8-4 3c2 5 5 8 10 10l3-4 8 3 0 6c-14 2-28-12-26-26z" fill="#1e7a3c"/></svg>
  <h3>Less Interviews</h3>
  <p>Experince fewer interviews with TRAVENOK to get the right job. Our platform matches you against your specilized project experinces, industry exposure and core PM skills.</p>
</div>

<div class="feature abs" style="left:66px;top:719px">
  <svg class="icon" viewBox="0 0 38 38" role="img" aria-label="Target icon"><circle cx="19" cy="19" r="16" fill="#d8322c"/><circle cx="19" cy="19" r="11" fill="#fff"/><circle cx="19" cy="19" r="7" fill="#2f87c6"/><circle cx="19" cy="19" r="3" fill="#f2b632"/><path d="M19 19L33 5" stroke="#444" stroke-width="2"/></svg>
  <h3>Transperency</h3>
  <p>In order to promote win-win scenarios for our clients and consultants, we provide 100% transparency in all our services.</p>
</div>

<div class="feature abs" style="left:376px;top:719px">
  <svg class="icon" viewBox="0 0 38 38" role="img" aria-label="Thumbs up icon"><rect x="3" y="18" width="9" height="16" rx="2" fill="#2b2b2b"/><rect x="13" y="16" width="20" height="18" rx="5" fill="#f0b07c"/><rect x="18" y="4" width="7" height="14" rx="3" fill="#f0b07c"/></svg>
  <h3>Make Better Decisions</h3>
  <p>Employers who have considered all their options and carefully made a decision to join us understand that we bring the highest caliber candidates for the jobs.</p>
</div>

<div class="resume-btn abs">Upload Your Resume</div>

<footer class="site-footer abs">
  <div class="footer-about abs">
    <h4>About</h4>
    <div class="brand">TRAVENOK</div>
    <div class="tagline">PROJECT MANAGEMENT CONSULTING</div>
    <p>Maecenas scelerisque purus risus, sit amet aliquet dui malesuada vel. Suspendisse libero urna, vestibulum pretium magna id, vulputate auctor metus. Sed porttitor maximus tincidunt. Fusce ultricies est ut ante.</p>
  </div>
  <div class="quick-links abs">
    <h4>Quick Links</h4>
    <ul><li>About Us</li><li>Services</li><li>How It Works?</li><li>Newsletter</li><li>Contact Us</li><li>Privacy Policy</li><li>Sitemap</li></ul>
  </div>
  <div class="footer-contact abs">
    <h4>Contact</h4>
    <p>Lorem ipsum dolor sit amet, consectetur adipiscing elit. Nu nc tincidunt, odio eget luctus luctus, sapien magna ultrices ligula, sed lacinia nibh lorem ac mauris.</p>
    <div class="contact-line"><svg width="11" height="9" viewBox="0 0 11 9"><rect width="11" height="9" rx="1" fill="#f37122"/><path d="M0.5 1l5 4 5-4" stroke="#fff" fill="none"/></svg>hello@travenok.example</div>
    <div class="contact-line"><svg width="11" height="11" viewBox="0 0 11 11"><circle cx="5.5" cy="5.5" r="5" fill="none" stroke="#f37122"/><path d="M3.5 3h1.2l.6 1.5-.8.6c.4.9 1 1.5 1.9 1.9l.6-.8 1.5.6v1.2C5.8 8.2 3.3 5.7 3.5 3z" fill="#f37122"/></svg>555 014 2290</div>
  </div>
</footer>

<div class="bottom-bar abs">
  <p class="copyright">Copyright © Travenok. All Rights Reserved.</p>
  <div class="social"><i></i><i></i><i></i><i></i></div>
</div>

</body>
</html>
```